Dew and Willow med spa needs an awesome eye catching billboard ad

We need a billboard ad design for a Med Spa with location sin Davenport and Windermere FL A medical spa where the beauty of nature meets the power of science to treat the whole person, mind, body and soul.

Marigold Radiance Med Spa is a medical spa where the beauty of nature meets the power of science to create gorgeous, youthful looking skin. Located in Davenport, Florida, but also serving Four Corners, Celebration, and Windermere, Florida, the talented professional team brings decades of experience in world-class skin care to provide holistic, science-backed aesthetic services and health coaching.

Industry/Entity Type

Spa

Colors
fbee3e
fece3e
eea4c8
e667a6
fbee3d

Requirements
Must have
• Locations in Davenport and Dr Phillips
Phone 407-555-0148
website www.dewandwillow-example.com

Boards for each:
Aesthetic Treatments
Cosmetic Injectables
Quoria facial
add color vs too many earthtones, to catch the eye perhaps using yellow, something that catches the eye and stands out from the normal everyday
Thank you!!!!
Nice to have
• Boards for each:
Aesthetic Treatments
Cosmetic Injectables
Quoria facial
add color vs too many earthtones, to catch the eye
photos that match services,
Thank you!!!!

```html
<!DOCTYPE html>
<html lang="en">
<head>
<meta charset="utf-8">
<title>Marigold Radiance Med Spa – Billboard</title>
<link rel="stylesheet" href="https://fonts.googleapis.com/css2?family=Cormorant+Garamond:wght@500;600&family=Tinos:wght@400;700&family=Marcellus&display=swap">
<style>
  :root {
    --page: #ecebe8;
    --board: #f8f8f7;
    --gold: #c2ab7c;
    --ink: #4a4a4a;
    --ink-dark: #3e3e3e;
    --mint: #8fd6cb;
    --yellow: #fbee3e;
    --yellow-warm: #fece3e;
    --pink-soft: #eea4c8;
    --pink: #e667a6;
    --photo-light: #f3ece4;
    --photo-warm: #e9c9a6;
    --photo-hair: #5a3b2c;
    --photo-top: #e5a58a;
  }
  * { margin: 0; padding: 0; box-sizing: border-box; }
  html, body { width: 1029px; height: 1200px; overflow: hidden; background: var(--page); }
  .billboard {
    position: absolute; left: 0; top: 342px;
    width: 1029px; height: 515px;
    background: var(--board); overflow: hidden;
  }
  .petals { position: absolute; border-radius: 50%; }
  .petals--top-left {
    left: -40px; top: -50px; width: 193px; height: 181px;
    background: radial-gradient(circle at 30% 30%, var(--pink-soft), rgba(238,164,200,0.35) 70%, transparent 72%);
  }
  .petals--top-right {
    left: 845px; top: 0; width: 230px; height: 242px;
    background: radial-gradient(circle at 50% 45%, var(--mint), rgba(143,214,203,0.4) 65%, transparent 70%);
    z-index: 2;
  }
  .petals--bottom-left {
    left: -20px; top: 443px; width: 124px; height: 110px;
    background: radial-gradient(circle at 45% 50%, var(--yellow-warm), rgba(254,206,62,0.35) 65%, transparent 70%);
  }
  .photo {
    position: absolute; left: 579px; top: 0; width: 450px; height: 515px;
    background:
      radial-gradient(ellipse 120px 150px at 190px 190px, var(--photo-warm), transparent 75%),
      radial-gradient(ellipse 170px 260px at 190px 300px, var(--photo-hair), transparent 70%),
      linear-gradient(180deg, var(--photo-light) 0%, var(--photo-light) 55%, var(--photo-top) 100%);
    -webkit-mask-image: linear-gradient(90deg, transparent 0, #000 60px);
            mask-image: linear-gradient(90deg, transparent 0, #000 60px);
  }
  .brand-mark {
    position: absolute; left: 274px; top: 38px;
    width: 80px; height: 80px; border-radius: 50%;
    border: 3px solid var(--gold);
  }
  .brand-name {
    position: absolute; left: 30px; width: 560px; text-align: center;
    font-family: "Cormorant Garamond", serif; font-weight: 500;
    color: var(--gold); text-transform: uppercase; white-space: nowrap;
  }
  .brand-name--main { top: 160px; font-size: 40px; letter-spacing: 5px; }
  .brand-name--sub { top: 218px; font-size: 24px; letter-spacing: 8px; }
  .website {
    position: absolute; left: 30px; width: 560px; top: 262px; text-align: center;
    font-family: "Tinos", serif; font-size: 20px; color: var(--ink-dark);
    text-transform: uppercase; letter-spacing: 0.3px; white-space: nowrap;
  }
  .locations {
    position: absolute; left: 30px; width: 560px; top: 296px; text-align: center;
    font-family: "Tinos", serif; font-weight: 700; font-size: 18px;
    color: var(--pink); text-transform: uppercase; letter-spacing: 2px; white-space: nowrap;
  }
  .locations .dot {
    display: inline-block; width: 8px; height: 8px; border-radius: 50%;
    background: var(--yellow-warm); margin: 0 12px; vertical-align: middle;
  }
  .service-band {
    position: absolute; left: 0; top: 340px; width: 600px; height: 50px;
    background: linear-gradient(90deg, var(--yellow-warm) 0%, var(--yellow) 40%, rgba(238,164,200,0.6) 80%, rgba(248,248,247,0) 100%);
  }
  .service-title {
    position: absolute; left: 49px; top: 343px;
    font-family: "Tinos", serif; font-weight: 700; font-size: 39px;
    color: var(--ink-dark); letter-spacing: 0.5px; white-space: nowrap;
  }
  .phone {
    position: absolute; left: 139px; top: 410px;
    font-family: "Marcellus", sans-serif; font-size: 52px;
    color: var(--ink); white-space: nowrap;
  }
</style>
</head>
<body>
  <main class="billboard">
    <div class="photo" role="img" aria-label="Photo of a woman in a straw hat and pink top, eyes closed in warm sunlight"></div>
    <div class="petals petals--top-left" role="img" aria-label="Soft pink flower decoration"></div>
    <div class="petals petals--top-right" role="img" aria-label="Soft mint flower decoration"></div>
    <div class="petals petals--bottom-left" role="img" aria-label="Soft yellow flower decoration"></div>

    <div class="brand-mark"></div>
    <h1 class="brand-name brand-name--main">Marigold Radiance</h1>
    <p class="brand-name brand-name--sub">Med Spa</p>
    <p class="website">www.dewandwillow-example.com</p>
    <p class="locations">Davenport<span class="dot"></span>Dr Phillips</p>

    <div class="service-band"></div>
    <h2 class="service-title">AESTHETIC TREATMENTS</h2>
    <p class="phone">407-555-0148</p>
  </main>
</body>
</html>
```